We are a recruitment company based in Norwich/Cambridge England.
I have included our company logo which we want to remain the same.

What we are looking for is a new creative Business card which will really stand out!!

Contact Information for Business Card

Harriet Dunmore
email: Harriet@plavex.co.uk
Address: Brackwell House
Fenmoor Enterprise Park
Partridge Way
Norwich
QB9 3KX
Tel:01632 960418

```html
<!DOCTYPE html>
<html lang="en">
<head>
<meta charset="utf-8">
<title>Plavex business card</title>
<link href="https://fonts.googleapis.com/css2?family=Lato:wght@400;700&display=swap" rel="stylesheet">
<style>
  :root {
    --green: #84c441;
    --green-dark: #6fb02e;
    --grey: #8e8e90;
    --grey-light: #a3a3a5;
    --white: #ffffff;
    --paper: #f6f6f4;
    --stage: #e9e7e2;
  }
  * { box-sizing: border-box; margin: 0; padding: 0; }
  html, body { width: 1200px; height: 886px; overflow: hidden; }
  body {
    background: var(--stage);
    font-family: "Lato", sans-serif;
    position: relative;
  }
  .card {
    position: absolute;
    top: 163px;
    width: 340px;
    height: 560px;
    border-radius: 22px;
    overflow: hidden;
    box-shadow: 0 10px 30px rgba(0,0,0,.18);
  }
  /* front */
  .card-front { left: 220px; background: var(--paper); }
  .front-brand {
    position: absolute;
    top: 0; left: 0; right: 0; height: 215px;
    display: flex; flex-direction: column; align-items: flex-end; justify-content: center;
    padding-right: 34px;
  }
  .brand-row { display: flex; align-items: center; gap: 12px; }
  .brand-dot { width: 40px; height: 40px; border-radius: 50%; background: var(--grey); }
  .brand-name { font-size: 46px; font-weight: 700; color: var(--green); letter-spacing: -.5px; line-height: 1; }
  .brand-tagline {
    margin-top: 6px;
    font-size: 10px; letter-spacing: 3px; color: var(--grey);
  }
  .front-panel {
    position: absolute;
    top: 215px; left: 0; right: 0; height: 295px;
    background: var(--green);
  }
  .icon-rail {
    position: absolute;
    top: 10px; left: 0; width: 44px; height: 270px;
    background: var(--grey-light);
    border-radius: 0 18px 18px 0;
    display: flex; flex-direction: column; align-items: center; justify-content: space-around;
    padding: 18px 0;
  }
  .icon-rail svg { width: 16px; height: 16px; fill: var(--white); }
  .contact {
    position: absolute;
    top: 40px; left: 68px;
    color: var(--white);
  }
  .contact-name { font-size: 22px; font-weight: 700; letter-spacing: .5px; }
  .contact-role { font-size: 14px; letter-spacing: 1px; margin-bottom: 14px; }
  .contact-line { font-size: 14px; line-height: 21px; }
  .contact-gap { height: 10px; }
  .front-foot { position: absolute; bottom: 0; left: 0; right: 0; height: 50px; background: var(--paper); }

  /* back */
  .card-back { left: 640px; background: var(--green); }
  .back-mark {
    position: absolute;
    top: 150px; left: 0; right: 0;
    display: flex; flex-direction: column; align-items: center; gap: 22px;
  }
  .back-dot { width: 120px; height: 120px; border-radius: 50%; background: var(--white); }
  .back-name { font-size: 40px; font-weight: 700; color: var(--white); letter-spacing: -.5px; }
  .back-web {
    position: absolute;
    left: 0; right: 0; bottom: 48px; height: 46px;
    background: var(--white);
    display: flex; align-items: center; justify-content: center;
    font-size: 14px; letter-spacing: 6px; color: #555;
  }
</style>
</head>
<body>
  <section class="card card-front">
    <div class="front-brand">
      <div class="brand-row">
        <span class="brand-dot"></span>
        <span class="brand-name">Plavex</span>
      </div>
      <span class="brand-tagline">Technology Recruitment</span>
    </div>

    <div class="front-panel">
      <div class="icon-rail">
        <svg viewBox="0 0 16 16" aria-label="person"><circle cx="8" cy="5" r="3.5"/><path d="M1.5 15c0-4 3-6 6.5-6s6.5 2 6.5 6z"/></svg>
        <svg viewBox="0 0 16 16" aria-label="location"><path d="M8 0a5.5 5.5 0 0 0-5.5 5.5C2.5 10 8 16 8 16s5.5-6 5.5-10.5A5.5 5.5 0 0 0 8 0zm0 8a2.5 2.5 0 1 1 0-5 2.5 2.5 0 0 1 0 5z"/></svg>
        <svg viewBox="0 0 16 16" aria-label="phone"><path d="M3.6 1 6 3.4 4.7 5.6c.9 2.2 2.6 3.9 4.7 4.8l2.2-1.3L14 11.4l-1.4 2.8C6.8 14.2 1.8 9.2 1 3z"/></svg>
        <svg viewBox="0 0 16 16" aria-label="email"><path d="M1 3h14v10H1zm1.5 1.2L8 8.6l5.5-4.4z"/></svg>
        <svg viewBox="0 0 16 16" aria-label="website"><path d="M8 1a7 7 0 1 0 0 14A7 7 0 0 0 8 1zm0 1.5c.8 0 1.8 1.6 2.1 4.5H5.9C6.2 4.1 7.2 2.5 8 2.5zM5.9 9h4.2c-.3 2.9-1.3 4.5-2.1 4.5S6.2 11.9 5.9 9z"/></svg>
      </div>
      <div class="contact">
        <p class="contact-name">HARRIET DUNMORE</p>
        <p class="contact-role">CEO/FOUNDER</p>
        <p class="contact-line">Brackwell House</p>
        <p class="contact-line">Fenmoor Enterprise Park</p>
        <p class="contact-line">Partridge Way, Norwich QB9 3KX</p>
        <div class="contact-gap"></div>
        <p class="contact-line">01632 960418</p>
        <p class="contact-line">Harriet@plavex.co.uk</p>
        <p class="contact-line">www.plavex.co.uk</p>
      </div>
    </div>
    <div class="front-foot"></div>
  </section>

  <section class="card card-back">
    <div class="back-mark">
      <span class="back-dot"></span>
      <span class="back-name">Plavex</span>
    </div>
    <div class="back-web">www.plavex.co.uk</div>
  </section>
</body>
</html>
```